Homepage layout for online ad network

Attached is our Valtro Media logo and updated brief (I can't seem to delete the old logo and brief, but they're no longer relevant).

This project was originally posted with a different logo and corporate name, but we have decided to stay with our current logo and name and redesign the site.

Your design is for a homepage only - design, no coding (I'll get someone else to take your PSD and code it).

Your homepage will make use of a Flash slider - BUT YOU ARE NOT REQUIRED TO PROVIDE THE FLASH. Instead, simply provide the layout and at least two static examples out of the four different sections that will eventually be in the slider.

Much of this design is based on the design of a competitor (listed in the brief).

Please ask whatever questions you need to in order to clarify instructions.
Updates

Project updated to include new logo (and correspondingly new color scheme).

Brief changed slightly.

Thank you for submitting designs for this project in the past.

After some internal strategy work, we have decided to retain our initial corporate identity, Valtro Media.

If you have submitted a design for the original brief and are available, please re-work your best prior design to reflect the color scheme in the newly uploaded logo.

Target Market(s)

This site is aimed primarily at young professionals who buy digital media on behalf of large advertisers.

Industry/Entity Type

Media

Requirements
Must have
• modern white space
Should not have
• no Flash outside of slider

```html
<!DOCTYPE html>
<html lang="en">
<head>
<meta charset="utf-8">
<title>Valtro Media – Homepage</title>
<link rel="stylesheet" href="https://fonts.googleapis.com/css2?family=Montserrat:ital,wght@0,400;0,500;0,600;0,700;1,400;1,600&family=Oswald:wght@300;400&family=Arimo:wght@400;700&display=swap">
<style>
  :root {
    --red: #c8102e;
    --red-deep: #8b1424;
    --red-bright: #dc0e27;
    --ink: #1c1c1c;
    --text: #333333;
    --panel: #f8f8f8;
    --lime: #cbd92c;
    --lime-light: #eef27a;
    --white: #ffffff;
    --rule: #5a5a5a;
  }
  * { box-sizing: border-box; margin: 0; padding: 0; }
  html, body { width: 1200px; height: 1050px; overflow: hidden; background: var(--white); }
  .page { position: relative; width: 1200px; height: 1050px; overflow: hidden; font-family: "Arimo", Arial, sans-serif; color: var(--text); }

  /* Header */
  .brand { position: absolute; left: 148px; top: 28px; display: flex; align-items: center; gap: 12px; }
  .brand-mark { width: 32px; height: 32px; background: var(--lime); }
  .brand-name { font-family: "Montserrat", sans-serif; font-weight: 500; font-size: 30px; color: var(--ink); letter-spacing: -0.5px; }
  .tagline { position: absolute; right: 119px; top: 11px; font-family: "Montserrat", sans-serif; font-weight: 600; font-size: 11.5px; color: var(--red); letter-spacing: 0.3px; }
  .main-nav { position: absolute; right: 118px; top: 63px; display: flex; }
  .main-nav a { display: block; padding: 0 14px; height: 28px; line-height: 28px; font-family: "Montserrat", sans-serif; font-weight: 700; font-size: 12px; color: var(--ink); text-decoration: none; letter-spacing: 0.3px; border-left: 1px solid #444; }
  .main-nav a:first-child { border-left: none; }
  .main-nav a:nth-child(2) { border-left-color: var(--red); }
  .main-nav a:last-child { padding-right: 0; }
  .header-rule { position: absolute; left: 0; top: 100px; width: 1200px; height: 2px; background: var(--red); }
  .header-pointer { position: absolute; left: 253px; top: 87px; width: 0; height: 0; border-left: 8px solid transparent; border-right: 8px solid transparent; border-bottom: 11px solid var(--red); }

  /* Hero band */
  .hero { position: absolute; left: 0; top: 105px; width: 1200px; height: 425px; background: linear-gradient(180deg, var(--red-bright) 0%, #b81227 55%, var(--red-deep) 100%); }
  .slide { position: absolute; left: 123px; top: 30px; width: 960px; height: 352px; background: linear-gradient(90deg, #f4f5f7 0%, #dfe3e8 100%); box-shadow: 0 6px 10px rgba(0,0,0,0.45); overflow: hidden; }
  .slide-accent { position: absolute; left: 0; top: 0; width: 72px; height: 352px; background: #b31e2e; }
  .slide-photo { position: absolute; right: 92px; top: 0; width: 365px; height: 352px; background: radial-gradient(ellipse at 55% 55%, #d9a98c 0%, #8a5a48 45%, #3a2520 75%, #e6eaf0 100%); }
  .slide-title { position: absolute; left: 104px; top: 120px; font-family: "Montserrat", sans-serif; font-weight: 700; font-size: 40px; color: var(--red); letter-spacing: 0.5px; line-height: 1; }
  .slide-sub { position: absolute; left: 106px; top: 164px; font-family: "Montserrat", sans-serif; font-weight: 500; font-size: 21px; line-height: 25px; color: var(--ink); letter-spacing: 0.6px; }
  .slide-arrow { position: absolute; top: 158px; }
  .slide-arrow.prev { left: 20px; }
  .slide-arrow.next { right: 18px; }
  .slide-dots { position: absolute; left: 526px; top: 396px; display: flex; gap: 13px; }
  .slide-dots span { width: 15px; height: 15px; border-radius: 50%; background: #1a1a1a; }
  .slide-dots span.active { background: var(--white); }

  /* Stat strip */
  .stat { position: absolute; left: 0; top: 552px; width: 1200px; text-align: center; }
  .stat-text { font-family: "Montserrat", sans-serif; font-size: 23px; letter-spacing: 1px; color: var(--ink); position: relative; left: -27px; }
  .stat-text .num { font-style: italic; font-weight: 400; }
  .stat-text .em { font-style: italic; font-weight: 700; }
  .stat-text .hl { color: var(--red-deep); font-weight: 500; }
  .stat-arrow { position: absolute; top: 560px; }
  .stat-arrow.prev { left: 172px; }
  .stat-arrow.next { left: 1020px; }

  /* Content panel */
  .panel { position: absolute; left: 118px; top: 600px; width: 960px; height: 406px; background: var(--panel); box-shadow: 0 10px 12px -6px rgba(0,0,0,0.35); }
  .about { position: absolute; left: 0; top: 0; width: 610px; }
  .about-heading { position: absolute; left: 6px; top: 18px; display: flex; align-items: center; gap: 12px; font-family: "Oswald", sans-serif; font-weight: 300; font-size: 24px; color: var(--ink); white-space: nowrap; }
  .about-heading .mark { width: 20px; height: 20px; background: var(--lime); }
  .about-heading strong { font-weight: 400; }
  .about-lead { position: absolute; left: 5px; top: 64px; width: 560px; font-size: 18px; line-height: 24px; color: var(--red); }
  .about-body { position: absolute; left: 4px; top: 121px; width: 545px; font-size: 14px; line-height: 24px; color: var(--text); }
  .about-rule { position: absolute; left: 4px; top: 290px; width: 577px; height: 1px; background: var(--rule); }
  .about-links { position: absolute; left: 2px; top: 310px; display: flex; list-style: none; font-family: "Montserrat", sans-serif; font-weight: 500; font-size: 12.5px; letter-spacing: 0.4px; color: var(--ink); }
  .about-links li { display: flex; align-items: center; gap: 5px; white-space: nowrap; }
  .about-links li + li { margin-left: 21px; }
  .about-links li:nth-child(3) { margin-left: 28px; }
  .about-links li:nth-child(4) { margin-left: 21px; }
  .about-links li:nth-child(5) { margin-left: 20px; }

  .news { position: absolute; left: 610px; top: 0; width: 350px; height: 350px; }
  .news-divider { position: absolute; left: 0; top: 40px; width: 12px; height: 320px; background: linear-gradient(90deg, rgba(0,0,0,0.10), rgba(0,0,0,0)); }
  .news-heading { position: absolute; left: 2px; top: 14px; width: 238px; height: 39px; background: linear-gradient(90deg, var(--lime-light) 0%, var(--lime) 100%); box-shadow: 1px 2px 3px rgba(0,0,0,0.35); font-family: "Oswald", sans-serif; font-weight: 300; font-size: 24px; line-height: 39px; color: var(--red); padding-left: 30px; }
  .news-list { position: absolute; left: 39px; top: 70px; width: 290px; list-style: none; }
  .news-list li { margin-bottom: 16px; }
  .news-date { display: block; font-weight: 700; font-size: 12px; color: var(--red); letter-spacing: 0.4px; line-height: 16px; }
  .news-text { display: block; font-size: 12px; line-height: 16px; color: var(--text); }

  .copyright { position: absolute; left: 0; top: 1021px; width: 1246px; text-align: center; font-size: 12px; color: var(--ink); }
</style>
</head>
<body>
<div class="page">

  <header class="site-header">
    <div class="brand"><span class="brand-mark"></span><span class="brand-name">Valtro Media</span></div>
    <p class="tagline">COMPANY TAGLINE GOES HERE</p>
    <nav class="main-nav">
      <a href="#">BEAUTY</a>
      <a href="#">COOKING</a>
      <a href="#">PARENTING</a>
      <a href="#">ENTERTAINMENT</a>
      <a href="#">VIDEO</a>
      <a href="#">CPC</a>
    </nav>
    <span class="header-pointer"></span>
    <span class="header-rule"></span>
  </header>

  <section class="hero">
    <div class="slide">
      <div class="slide-accent"></div>
      <div class="slide-photo" role="img" aria-label="Beauty campaign photo of a woman with yellow flowers in her hair"></div>
      <h2 class="slide-title">BEAUTY</h2>
      <p class="slide-sub">SITE SPECIFIC CAMPAIGNS<br>AT RON PRICES</p>
      <svg class="slide-arrow prev" width="30" height="52" viewBox="0 0 30 52" aria-hidden="true"><path d="M28 2 L10 26 L28 50 L18 50 L2 26 L18 2 Z" fill="#1a1a1a"/></svg>
      <svg class="slide-arrow next" width="30" height="52" viewBox="0 0 30 52" aria-hidden="true"><path d="M2 2 L20 26 L2 50 L12 50 L28 26 L12 2 Z" fill="#1a1a1a"/></svg>
    </div>
    <div class="slide-dots"><span class="active"></span><span></span><span></span><span></span><span></span><span></span></div>
  </section>

  <section class="stat">
    <p class="stat-text"><span class="num">15</span> <span class="em">MILLION</span> <span class="hl">CANADIANS</span></p>
  </section>
  <svg class="stat-arrow prev" width="22" height="18" viewBox="0 0 22 20" aria-hidden="true"><path d="M10 2 L2 10 L10 18 M20 2 L12 10 L20 18" fill="none" stroke="#b3152a" stroke-width="4"/></svg>
  <svg class="stat-arrow next" width="22" height="18" viewBox="0 0 22 20" aria-hidden="true"><path d="M2 2 L10 10 L2 18 M12 2 L20 10 L12 18" fill="none" stroke="#b3152a" stroke-width="4"/></svg>

  <main class="panel">
    <section class="about">
      <h3 class="about-heading"><span class="mark"></span><span>ABOUT <strong>VALTRO MEDIA</strong></span></h3>
      <p class="about-lead">Lorem ipsum dolor sit amet, consectetur adipiscing elit. Mauris dignissim nulla pharetra risus iaculis at consequat turpis vulputate.</p>
      <p class="about-body">Sed scelerisque magna ut quam scelerisque dictum. Morbi purus quam, sodales id vehicula non, ultricies vitae justo. Vivamus sed augue ut elit dapibus adipiscing vel in elit. Mauris adipiscing, elit a laoreet eleifend, orci lacus condimentum enim, vitae venenatis enim velit ac dolor. Nullam augue mauris, tincidunt et bibendum nec, consequat ut dui. Sed id ante in purus vulputate adipiscing ac non justo. Nulla libero sem, venenatis in fringilla pulvinar, ornare ac diam.</p>
      <span class="about-rule"></span>
      <ul class="about-links">
        <li>ABOUT US <svg width="12" height="10" viewBox="0 0 12 10"><path d="M0 5 H10 M6 1 L10 5 L6 9" fill="none" stroke="#c8102e" stroke-width="2"/></svg></li>
        <li>CONTACT US <svg width="12" height="10" viewBox="0 0 12 10"><path d="M0 5 H10 M6 1 L10 5 L6 9" fill="none" stroke="#c8102e" stroke-width="2"/></svg></li>
        <li>MANAGEMENT TEAM <svg width="12" height="10" viewBox="0 0 12 10"><path d="M0 5 H10 M6 1 L10 5 L6 9" fill="none" stroke="#c8102e" stroke-width="2"/></svg></li>
        <li>NEWS <svg width="12" height="10" viewBox="0 0 12 10"><path d="M0 5 H10 M6 1 L10 5 L6 9" fill="none" stroke="#c8102e" stroke-width="2"/></svg></li>
        <li>CAREERS <svg width="12" height="10" viewBox="0 0 12 10"><path d="M0 5 H10 M6 1 L10 5 L6 9" fill="none" stroke="#c8102e" stroke-width="2"/></svg></li>
      </ul>
    </section>

    <aside class="news">
      <span class="news-divider"></span>
      <h3 class="news-heading">VALTRO NEWS</h3>
      <ul class="news-list">
        <li><span class="news-date">JANUARY 15, 2011</span><span class="news-text">Valtro Media unveils new web site design and digital strategy</span></li>
        <li><span class="news-date">DECEMBER 22, 2010</span><span class="news-text">Valtro Media featured in Founderly.com as one of the fastest grown online ad agencies.</span></li>
        <li><span class="news-date">NOVEMBER 15, 2010</span><span class="news-text">As RTB Goes Mainstream, Display Services Try To Pull Publishers Along</span></li>
        <li><span class="news-date">NOVEMBER 9, 2010</span><span class="news-text">Morbi purus quam, sodales id vehicula non, ultricies vitae justo</span></li>
      </ul>
    </aside>
  </main>

  <footer class="copyright">Copyright 2011 Valtro Media. All Rights Reserved</footer>
</div>
</body>
</html>
```